Business card design needed

I would like a one sided black business card with the information provided above. Refer to my website www.brightvolleyracquets.com.au for an example of colors I have used for my site, would like to keep this consistent for my business cards also, I will upload my logo below.

I am a new small business that provides tennis customers with racquet re stringing, tennis strings and accessories.

Industry/Entity Type

Small Business

Contact Information for Business Card

Bright Volley Tennis

Owen Whitby
Managing Director

brightvolleyracquets@mailbox.example
www.brightvolleyracquets.com.au
0491 726 305

Racquet Restringing/Tennis Strings/Accessories

Requirements
Must have
• Must have my logo and card must be black

```html
<!DOCTYPE html>
<html lang="en">
<head>
<meta charset="utf-8">
<title>Bright Volley Tennis – Business Card</title>
<link href="https://fonts.googleapis.com/css2?family=Questrial&display=swap" rel="stylesheet">
<style>
  :root {
    --backdrop: #e9e6e1;
    --card: #000000;
    --lime: #b5d334;
    --navy: #2f4f7f;
    --white: #ffffff;
    --font: "Questrial", "Century Gothic", sans-serif;
  }
  * { margin: 0; padding: 0; box-sizing: border-box; }
  html, body {
    width: 1200px;
    height: 475px;
    overflow: hidden;
    background: var(--backdrop);
    font-family: var(--font);
  }
  .canvas {
    position: relative;
    width: 1200px;
    height: 475px;
  }
  .card {
    position: absolute;
    width: 545px;
    height: 311px;
    background: var(--card);
    border-radius: 13px;
    overflow: hidden;
  }
  .card--front { left: 39px; top: 81px; }
  .card--back { left: 607px; top: 84px; }

  .brand {
    position: absolute;
    display: flex;
    align-items: center;
    gap: 8px;
    color: var(--lime);
    white-space: nowrap;
  }
  .brand__dot {
    display: block;
    border-radius: 50%;
    background: var(--lime);
  }
  .card--front .brand {
    left: 20px;
    top: 128px;
    font-size: 20px;
  }
  .card--front .brand__dot { width: 16px; height: 16px; }
  .card--back .brand {
    left: 0;
    right: 0;
    top: 110px;
    justify-content: center;
    font-size: 31px;
    gap: 12px;
  }
  .card--back .brand__dot { width: 24px; height: 24px; }

  .person {
    position: absolute;
    left: 285px;
    top: 72px;
    color: var(--lime);
  }
  .person__name {
    font-size: 21px;
    letter-spacing: 0.3px;
    font-weight: 400;
    text-transform: uppercase;
    line-height: 1.1;
  }
  .person__role {
    font-size: 13.5px;
    margin-top: 3px;
  }

  .contacts {
    position: absolute;
    left: 278px;
    top: 158px;
    list-style: none;
  }
  .contacts__item {
    display: flex;
    align-items: center;
    height: 19px;
    color: var(--white);
    font-size: 12.5px;
    letter-spacing: 0;
    white-space: nowrap;
  }
  .contacts__icon {
    width: 11px;
    height: 11px;
    margin-right: 10px;
    fill: var(--lime);
    flex: none;
  }

  .stripe {
    position: absolute;
    top: 276px;
    height: 11px;
  }
  .stripe--lime { left: 0; width: 279px; background: var(--lime); }
  .stripe--navy { left: 285px; right: 0; background: var(--navy); }

  .card__web {
    position: absolute;
    left: 0;
    right: 0;
    top: 252px;
    text-align: center;
    color: var(--white);
    font-size: 14.5px;
    letter-spacing: 2px;
  }
</style>
</head>
<body>
<main class="canvas">
  <section class="card card--front" aria-label="Business card front">
    <div class="brand">
      <span class="brand__dot"></span>
      <span class="brand__name">Bright Volley Tennis</span>
    </div>

    <div class="person">
      <h1 class="person__name">Owen Whitby</h1>
      <p class="person__role">Managing Director</p>
    </div>

    <ul class="contacts">
      <li class="contacts__item">
        <svg class="contacts__icon" viewBox="0 0 24 24" aria-hidden="true"><path d="M6.6 10.8a15.1 15.1 0 0 0 6.6 6.6l2.2-2.2c.3-.3.7-.4 1-.2 1.1.4 2.3.6 3.6.6.6 0 1 .4 1 1V20c0 .6-.4 1-1 1C10.6 21 3 13.4 3 4c0-.6.4-1 1-1h3.5c.6 0 1 .4 1 1 0 1.3.2 2.5.6 3.6.1.3 0 .7-.2 1z"/></svg>
        <span>0491 726 305</span>
      </li>
      <li class="contacts__item">
        <svg class="contacts__icon" viewBox="0 0 24 24" aria-hidden="true"><path d="M2 5h20v14H2z M3.5 6.5 12 13l8.5-6.5" stroke="#000" stroke-width="1.6"/></svg>
        <span>brightvolleyracquets@mailbox.example</span>
      </li>
      <li class="contacts__item">
        <svg class="contacts__icon" viewBox="0 0 24 24" aria-hidden="true"><circle cx="12" cy="12" r="10"/><path d="M2 12h20M12 2c3 3 3 17 0 20M12 2c-3 3-3 17 0 20" stroke="#000" stroke-width="1.6" fill="none"/></svg>
        <span>www.brightvolleyracquets.com.au</span>
      </li>
    </ul>

    <div class="stripe stripe--lime"></div>
    <div class="stripe stripe--navy"></div>
  </section>

  <section class="card card--back" aria-label="Business card back">
    <div class="brand">
      <span class="brand__dot"></span>
      <span class="brand__name">Bright Volley Tennis</span>
    </div>
    <p class="card__web">www.brightvolleyracquets.com.au</p>
  </section>
</main>
</body>
</html>
```